Design NEW business card

We would like a business card using the colour deep red wine or dark navy blue textured background (patterned or not, open to suggestions) with a high gloss debossed rose gold/copper RM Roland Mercer Jewellery business name (Provided). I have included images for your review we would like to keep our currently logo and business name on the front but you can change the layout and positioning. For the back of the card we are open to all suggestions/variations.
Business
Use our current RM Roland Mercer Jewellery logo (Provided image)

```html
<!DOCTYPE html>
<html lang="en">
<head>
<meta charset="utf-8">
<title>Roland Mercer Jewellery – Business Card</title>
<link rel="stylesheet" href="https://fonts.googleapis.com/css2?family=Montserrat:wght@400;600&family=Open+Sans:wght@400;600;700&display=swap">
<style>
  :root {
    --backdrop: #3a3431;
    --wine: #5a2230;
    --wine-edge: #4a1b27;
    --rose-gold: #c89a82;
    --silver: #d6c9cc;
    --text-light: #f4ecee;
    --gold: #b48a5a;
  }
  * { margin: 0; padding: 0; box-sizing: border-box; }
  html, body {
    width: 1200px; height: 864px; overflow: hidden;
    background: var(--backdrop);
  }
  .stage { position: relative; width: 1200px; height: 864px; }
  .card {
    position: absolute;
    width: 560px; height: 320px;
    background: var(--wine);
    border: 1px solid var(--wine-edge);
    box-shadow: 0 10px 24px rgba(0,0,0,0.45);
  }
  .card-front { left: 50px; top: 60px; }
  .card-back { left: 590px; top: 460px; }

  .brand {
    font-family: "Montserrat", sans-serif;
    font-weight: 400;
    text-transform: uppercase;
    letter-spacing: 0.16em;
    display: flex; align-items: center; gap: 12px;
  }
  .brand-dot {
    width: 10px; height: 10px; border-radius: 50%;
    background: currentColor; flex: none;
  }
  .card-front .brand {
    position: absolute; left: 70px; top: 120px;
    color: var(--silver); font-size: 22px;
  }
  .card-front .website {
    position: absolute; left: 70px; top: 200px;
    font-family: "Open Sans", sans-serif; font-size: 15px;
    letter-spacing: 0.22em; color: var(--silver);
  }
  .card-back .brand {
    position: absolute; left: 40px; top: 60px;
    color: var(--rose-gold); font-size: 19px;
  }
  .contact {
    position: absolute; left: 40px; top: 150px;
    font-family: "Open Sans", sans-serif; font-size: 13px;
    line-height: 1.45; color: var(--text-light);
  }
  .contact .web { font-weight: 700; font-size: 14px; letter-spacing: 0.06em; }
  .person {
    position: absolute; right: 36px; bottom: 34px; text-align: left;
    font-family: "Open Sans", sans-serif;
  }
  .person-name { font-weight: 700; font-size: 14px; color: var(--gold); text-transform: uppercase; }
  .person-title { font-size: 13px; color: var(--text-light); text-transform: uppercase; }
</style>
</head>
<body>
<main class="stage">
  <section class="card card-front">
    <div class="brand"><span class="brand-dot"></span>Roland Mercer Jewellery</div>
    <p class="website">www.mercerfine.com</p>
  </section>

  <section class="card card-back">
    <div class="brand"><span class="brand-dot"></span>Roland Mercer Jewellery</div>
    <address class="contact">
      214 Larkspur Row<br>
      Juneau, Alaska 99801<br>
      P. 907 555 0142<br>
      E. hello@mercerfine.com<br>
      <span class="web">www.mercerfine.com</span>
    </address>
    <div class="person">
      <p class="person-name">Daniel Hart</p>
      <p class="person-title">CEO/Founder</p>
    </div>
  </section>
</main>
</body>
</html>
```